Local Roofing/Construction company business needs new biz card design

We need a new business card design, current cards are from the start of this operation and generic at best. We are a local Construction Company (General Contractor) with a majority of our work originating from insurance claims-exterior finish work is the main focus (Roofs-Siding-Gutters etc). Heavily involved with homeowners and the low ball offers they receive from insurance company's after a insurable event takes place. I have attached some of our original logo file(s) below.

```html
<!DOCTYPE html>
<html lang="en">
<head>
<meta charset="UTF-8">
<title>T-Crest Builders – Business Card</title>
<link rel="stylesheet" href="https://fonts.googleapis.com/css2?family=Montserrat:wght@400;500;700;800&display=swap">
<style>
  :root {
    --bg: #1b1b1e;
    --card-back: #0c0c0d;
    --card-front: #2a2a2d;
    --green: #2bd46a;
    --white: #f4f4f4;
    --grey: #d8d8d8;
    --silver: #a9a9ad;
  }
  * { box-sizing: border-box; margin: 0; padding: 0; }
  html, body { width: 1200px; height: 900px; overflow: hidden; }
  body {
    background: var(--bg);
    font-family: "Montserrat", Arial, sans-serif;
    position: relative;
  }
  .card {
    position: absolute;
    width: 520px;
    height: 298px;
    border-radius: 18px;
    overflow: hidden;
    box-shadow: 0 18px 40px rgba(0,0,0,.55);
  }
  .card::after {
    content: "";
    position: absolute;
    left: 0; right: 0; bottom: 0;
    height: 5px;
    background: var(--green);
  }

  /* Back side */
  .card--back { left: 70px; top: 110px; background: var(--card-back); }
  .card__texture {
    position: absolute; inset: 0;
    background: linear-gradient(100deg, #8d8d92 0%, #4a4a4f 30%, #1e1e21 60%, #0c0c0d 85%);
  }
  .card__brandmark {
    position: absolute;
    right: 40px; top: 120px;
    display: flex; align-items: center; gap: 10px;
    font-weight: 800;
    font-size: 22px;
    letter-spacing: .04em;
    color: var(--green);
  }
  .card__brandmark .dot {
    width: 14px; height: 14px; background: var(--green);
  }

  /* Front side */
  .card--front { left: 610px; top: 480px; background: var(--card-front); }
  .wordmark {
    position: absolute; left: 34px; top: 34px;
    font-weight: 800;
    color: var(--white);
    font-size: 30px;
    line-height: 1.02;
    letter-spacing: .02em;
    text-transform: uppercase;
  }
  .monogram-area {
    position: absolute; right: 30px; top: 34px;
    width: 170px; height: 150px;
    background: linear-gradient(135deg, #55555a 0%, #1a1a1c 70%);
    border-radius: 4px;
  }
  .contact {
    position: absolute; left: 34px; top: 128px;
    padding-left: 14px;
    border-left: 4px solid var(--green);
  }
  .contact__name { font-weight: 700; font-size: 20px; color: var(--green); }
  .contact__role { font-size: 12px; color: var(--grey); margin-bottom: 8px; }
  .contact__address { font-size: 11.5px; color: var(--grey); line-height: 1.35; margin-bottom: 8px; }
  .contact__list { list-style: none; font-size: 11.5px; color: var(--grey); }
  .contact__list li { display: flex; align-items: center; gap: 8px; line-height: 1.5; }
  .contact__list svg { width: 11px; height: 11px; fill: var(--green); flex: none; }
</style>
</head>
<body>

<section class="card card--back" aria-label="Card back">
  <div class="card__texture" role="img" aria-label="Repeating brand monogram pattern in silver fading to black"></div>
  <div class="card__brandmark"><span class="dot"></span>T-CREST BUILDERS</div>
</section>

<section class="card card--front" aria-label="Card front">
  <div class="wordmark">T-Crest<br>Builders</div>
  <div class="monogram-area" role="img" aria-label="Large glossy brand monogram"></div>

  <div class="contact">
    <p class="contact__name">Daniel Brooks</p>
    <p class="contact__role">Owner</p>
    <p class="contact__address">245 Oak Ridge Ln<br>Fairview, MO 63012</p>
    <ul class="contact__list">
      <li>
        <svg viewBox="0 0 24 24" aria-hidden="true"><path d="M6.6 10.8a15.1 15.1 0 0 0 6.6 6.6l2.2-2.2a1 1 0 0 1 1-.25 11.4 11.4 0 0 0 3.6.57 1 1 0 0 1 1 1V20a1 1 0 0 1-1 1A17 17 0 0 1 3 4a1 1 0 0 1 1-1h3.5a1 1 0 0 1 1 1c0 1.25.2 2.45.57 3.57a1 1 0 0 1-.25 1z"/></svg>
        555-214-0187
      </li>
      <li>
        <svg viewBox="0 0 24 24" aria-hidden="true"><path d="M2 5h20v14H2z M2 5l10 8 10-8" fill="none" stroke="#2bd46a" stroke-width="2.5"/></svg>
        info@tcrestbuilders.com
      </li>
      <li>
        <svg viewBox="0 0 24 24" aria-hidden="true"><circle cx="12" cy="12" r="10" fill="none" stroke="#2bd46a" stroke-width="2.5"/><path d="M2 12h20M12 2c3 3 3 17 0 20M12 2c-3 3-3 17 0 20" fill="none" stroke="#2bd46a" stroke-width="2"/></svg>
        www.tcrestbuilders.com
      </li>
    </ul>
  </div>
</section>

</body>
</html>
```